uk based ecommerce website requires fresh look ,high quality look and feel

we are a web based company selling eco friendly ground reinforcement grids to diy and construction sectors
our existing website is www.pondermeshpaths.co.uk ,

we have already updated the logo so that is the branding sorted .so we need a ecommerce website that is very much up-to date in design and layout and which has content management system for ease of use so that we can add products and information as required.

Use current logo as reference for colour scheme.
www.pondermeshpaths.co.uk

The current website has 6 pages accessible through the navigation bar, I would now like 5 pages, removing the need for the Trade Enquiries page possibly have it with along with contact us.

Target Market(s)

construction industry , diy end users,
retail market, landscapers, gardeners

Industry/Entity Type

Construction

Font styles to use
Other font styles liked:
• logo font prometo

Colors
f78f20
9bcb3c

Requirements
Must have
• logo colours and logo design in website with cms responsive design for tablet and mobile devices
• expect content to work flawlessly and look great across all devices
• HTML 5 custom design with coding as required
• must have good experiance in ecommerce website design
• eye catching, high quality look and feel and very user friedly ,very up-to date.
Nice to have
• picture slider show
• explain in writing what exactly i am getting in my ecommerce website
Should not have
• plain , basic design , old fashion looking ,cheap look

```html
<!DOCTYPE html>
<html lang="en">
<head>
<meta charset="utf-8">
<title>Contact Us – Pondermesh</title>
<link href="https://fonts.googleapis.com/css2?family=Open+Sans:wght@400;600;700&family=Raleway:wght@500&display=swap" rel="stylesheet">
<style>
:root{
  --orange:#f7891f;
  --green:#8cc63f;
  --dark:#2b2624;
  --footer:#2a2523;
  --text:#4a4a4a;
  --muted:#6d6d6d;
  --line:#dcdcdc;
  --white:#fff;
}
*{box-sizing:border-box;margin:0;padding:0}
html,body{width:1200px;height:1136px;overflow:hidden;background:var(--white)}
body{font-family:"Open Sans",sans-serif;color:var(--text);position:relative}
.abs{position:absolute}
/* header */
.brand{left:89px;top:22px;display:flex;align-items:center;gap:8px}
.brand-mark{width:28px;height:28px;background:var(--green)}
.brand-name{font-weight:700;font-size:17px;color:var(--orange);letter-spacing:.5px}
.search{left:398px;top:18px;width:288px;height:42px;border:1px solid #ccc;border-radius:21px;overflow:hidden;display:flex}
.search span{flex:1;font-size:12px;color:#666;padding:12px 18px}
.search-btn{width:46px;background:var(--orange);display:flex;align-items:center;justify-content:center}
.tele{left:760px;top:26px}
.tele-label{left:805px;top:22px;font-size:17px;color:#222;letter-spacing:1px}
.tele-sub{left:805px;top:45px;font-size:13px;color:#333}
.tele-nums{right:89px;top:16px;text-align:right;font-weight:700;font-size:18.5px;line-height:23px}
.o{color:var(--orange)}.g{color:var(--green)}
/* nav */
.nav{left:0;top:79px;width:1200px;height:47px;background:var(--dark)}
.nav ul{list-style:none;display:flex;position:absolute;left:89px;top:0;height:47px}
.nav li{font-size:14px;color:#fff;line-height:47px;margin-right:35px}
.nav li.active{background:var(--orange);padding:0 16px;margin-left:-16px;margin-right:0}
.account{right:60px;top:79px;height:47px;display:flex;align-items:center;gap:12px;color:#fff;font-size:14px}
.badge{width:14px;height:14px;border-radius:50%;background:var(--green);font-size:9px;color:#fff;text-align:center;line-height:14px;position:absolute;right:-6px;top:-8px}
/* hero */
.hero{left:0;top:126px;width:1200px;height:178px;background:linear-gradient(90deg,#f2f1ee 0%,#e7e4de 45%,#b8aa95 70%,#8a7a60 80%,#d8d4cc 100%)}
.hero-title{left:90px;top:186px;font-family:"Raleway",sans-serif;font-weight:500;font-size:37px;line-height:44px;color:#222}
.crumb{left:89px;top:230px;font-size:13px;color:#222;display:flex;align-items:center;gap:8px}
/* contact */
.c-title{left:88px;top:336px;font-size:26px;color:#222;font-weight:400}
.c-intro{left:88px;top:370px;width:500px;font-size:13px;line-height:21px;color:#444}
.field{border:1px solid var(--line);font-size:13px;color:#777;padding:14px 20px;height:43px}
.captcha-label{left:89px;top:706px;width:260px;font-size:13px;line-height:19px;color:#444}
.submit{left:89px;top:753px;width:587px;height:43px;background:var(--orange);color:#fff;font-weight:600;font-size:13px;text-align:center;line-height:43px}
.info{left:712px;font-size:12.8px;color:#444;line-height:21px}
.info-row{display:flex;gap:14px;align-items:flex-start}
.info-row svg{flex:none;margin-top:3px}
.co-head{left:717px;top:575px;font-size:15px;font-weight:600;color:#222}
.co-list{left:717px;top:604px;width:400px;font-size:12.4px;line-height:22.3px;color:#666}
/* footer */
.footer{left:0;top:851px;width:1200px;height:236px;background:var(--footer)}
.f-head{top:880px;font-size:15px;color:#fff}
.f-rule{top:908px;height:1px;background:#4a4441}
.f-text{font-size:12px;color:#fff;line-height:18px}
.thumb{width:75px;height:57px}
.social{top:929px;width:40px;height:40px;border-radius:50%}
.card{top:988px;width:46px;height:28px;background:#fff;border-radius:2px;font-size:9px;font-weight:600;color:var(--dark);text-align:center;line-height:28px}
.bottom{left:0;top:1087px;width:1200px;height:49px;background:var(--orange)}
.bottom-left{left:89px;top:1103px;font-size:12px;color:#fff}
.bottom-links{right:89px;top:1104px;font-size:12px;color:#fff;display:flex;gap:24px}
</style>
</head>
<body>

<header>
  <div class="abs brand"><span class="brand-mark"></span><span class="brand-name">PONDERMESH</span></div>
  <div class="abs search"><span>Search</span>
    <div class="search-btn"><svg width="20" height="20" viewBox="0 0 20 20"><circle cx="8" cy="8" r="6" fill="none" stroke="#fff" stroke-width="2"/><line x1="12.5" y1="12.5" x2="18" y2="18" stroke="#fff" stroke-width="2.4"/></svg></div>
  </div>
  <svg class="abs tele" width="34" height="34" viewBox="0 0 24 24"><path fill="#f7891f" d="M6.6 10.8c1.4 2.8 3.8 5.1 6.6 6.6l2.2-2.2c.3-.3.7-.4 1-.2 1.1.4 2.3.6 3.6.6.6 0 1 .4 1 1V20c0 .6-.4 1-1 1C10.6 21 3 13.4 3 4c0-.6.4-1 1-1h3.5c.6 0 1 .4 1 1 0 1.3.2 2.5.6 3.6.1.3 0 .7-.2 1z"/></svg>
  <div class="abs tele-label">TELE</div>
  <div class="abs tele-sub">hour messaging service 24</div>
  <div class="abs tele-nums"><div class="o">0100-555-0182</div><div class="g">0800-555-0145</div></div>
</header>

<nav class="abs nav">
  <ul><li>Home</li><li>Shop</li><li>About Us</li><li>Ground Solutions</li><li>Pondermesh</li><li class="active">Contact Us</li></ul>
</nav>
<div class="abs account"><span>Login | Register</span>
  <span style="position:relative"><svg width="24" height="20" viewBox="0 0 24 20"><path d="M1 2h4l3 11h12l3-8H7" fill="none" stroke="#f7891f" stroke-width="2"/><circle cx="9" cy="17" r="2" fill="#f7891f"/><circle cx="19" cy="17" r="2" fill="#f7891f"/></svg><span class="badge">0</span></span>
</div>

<div class="abs hero" role="img" aria-label="Photo of a ground worker laying reinforcement grid at an airfield"></div>
<h1 class="abs hero-title">Contact Us</h1>
<div class="abs crumb"><svg width="14" height="12" viewBox="0 0 14 12"><path d="M7 0L0 6h2v6h4V8h2v4h4V6h2z" fill="#222"/></svg>Home <span>/</span> Contact</div>

<main>
  <h2 class="abs c-title">Contact us</h2>
  <p class="abs c-intro">If you require more information please fill in the form below. You will be contacted as soon as possible.Please fill in all required fields.</p>
  <div class="abs field" style="left:89px;top:426px;width:290px">Your name</div>
  <div class="abs field" style="left:386px;top:426px;width:290px">Your email</div>
  <div class="abs field" style="left:89px;top:475px;width:290px">Phone number</div>
  <div class="abs field" style="left:386px;top:475px;width:290px;display:flex;justify-content:space-between"><span>How did you hear about us?</span><svg width="10" height="8" viewBox="0 0 10 8" style="margin-top:4px"><path d="M0 0h10L5 8z" fill="#333"/></svg></div>
  <div class="abs field" style="left:87px;top:524px;width:589px;height:172px"></div>
  <p class="abs captcha-label">To avoid automatic submissions, please answer this captcha question</p>
  <div class="abs field" style="left:386px;top:703px;width:290px;padding:0">
    <div class="abs" role="img" aria-label="Captcha image" style="right:8px;top:10px;width:70px;height:22px;background:linear-gradient(90deg,#fff,#eee,#fff)"></div>
  </div>
  <div class="abs submit">SUBMIT</div>

  <div class="abs info" style="top:370px">
    <div class="info-row"><svg width="12" height="16" viewBox="0 0 12 16"><path d="M6 0a6 6 0 0 0-6 6c0 4.5 6 10 6 10s6-5.5 6-10a6 6 0 0 0-6-6zm0 8.5A2.5 2.5 0 1 1 6 3.5a2.5 2.5 0 0 1 0 5z" fill="#f7891f"/></svg><span>PONDERMESH ECO SOLUTIONS LTD Brackenfold House,<br>Kelmere Ind Est, Ashbridge, AB1 2CD.</span></div>
    <div class="info-row" style="margin-top:5px"><svg width="14" height="10" viewBox="0 0 14 10"><rect x=".5" y=".5" width="13" height="9" fill="none" stroke="#f7891f"/><path d="M.5.5L7 6l6.5-5.5" fill="none" stroke="#f7891f"/></svg><span>E-MAIL : sales@pondermeshpaths.co.uk</span></div>
    <div class="info-row" style="margin-top:1px"><svg width="14" height="13" viewBox="0 0 14 13"><rect x=".5" y="1.5" width="13" height="11" fill="none" stroke="#f7891f"/><rect x=".5" y="1.5" width="13" height="3" fill="#f7891f"/><g fill="#f7891f"><rect x="3" y="6" width="2" height="2"/><rect x="6" y="6" width="2" height="2"/><rect x="9" y="6" width="2" height="2"/><rect x="3" y="9" width="2" height="2"/><rect x="6" y="9" width="2" height="2"/></g></svg><span>CONTACT US BETWEEN :9.30am - 4.30pm Mon - Fri</span></div>
    <p style="margin:16px 0 0 5px;width:300px">You can also leave a recorded message with our answering service</p>
    <div class="info-row" style="margin:6px 0 0 3px"><svg width="14" height="14" viewBox="0 0 24 24"><path fill="#f7891f" d="M6.6 10.8c1.4 2.8 3.8 5.1 6.6 6.6l2.2-2.2c.3-.3.7-.4 1-.2 1.1.4 2.3.6 3.6.6.6 0 1 .4 1 1V20c0 .6-.4 1-1 1C10.6 21 3 13.4 3 4c0-.6.4-1 1-1h3.5c.6 0 1 .4 1 1 0 1.3.2 2.5.6 3.6.1.3 0 .7-.2 1z"/></svg><span>0100-555-0182</span></div>
    <div class="info-row" style="margin:2px 0 0 3px"><svg width="14" height="14" viewBox="0 0 24 24"><path fill="#f7891f" d="M6.6 10.8c1.4 2.8 3.8 5.1 6.6 6.6l2.2-2.2c.3-.3.7-.4 1-.2 1.1.4 2.3.6 3.6.6.6 0 1 .4 1 1V20c0 .6-.4 1-1 1C10.6 21 3 13.4 3 4c0-.6.4-1 1-1h3.5c.6 0 1 .4 1 1 0 1.3.2 2.5.6 3.6.1.3 0 .7-.2 1z"/></svg><span>0800-555-0145</span></div>
  </div>
  <h3 class="abs co-head">Company Info:</h3>
  <div class="abs co-list">
    <div style="white-space:nowrap">Companys registration name = PONDERMESH ECO SOLUTIONS LTD</div>
    Place of registration =ENGLAND GB<br>
    Registered office address = 3rd Floor, 14 Marlowe Street, London, EC1 9ZZ<br>
    Company registration number = GB: 01234567<br>
    Contact telephone number = 01000-555-182<br>
    Email address. = sales@pondermeshpaths.co.uk
  </div>
</main>

<footer>
  <div class="abs footer"></div>
  <div class="abs f-head" style="left:88px">About Us</div>
  <div class="abs f-head" style="left:343px">Gallery</div>
  <div class="abs f-head" style="left:598px">Contact Info</div>
  <div class="abs f-head" style="left:856px">Follow Us</div>
  <div class="abs f-rule" style="left:88px;width:238px"></div>
  <div class="abs f-rule" style="left:343px;width:237px"></div>
  <div class="abs f-rule" style="left:598px;width:236px"></div>
  <div class="abs f-rule" style="left:856px;width:234px"></div>

  <div class="abs f-text" style="left:87px;top:928px;width:230px">Consectetuer adipiscing elit. Aenean commodo ligula eget dolor.</div>
  <div class="abs f-text" style="left:89px;top:968px;width:230px">consectetuer adipiscing elit. Aenean commodo ligula eget dolor. Aenean massa. Cum sociis natoque penatibus et magnis dis parturient montes.</div>

  <div class="abs thumb" role="img" aria-label="Grid being laid on gravel" style="left:344px;top:927px;background:#8d8272"></div>
  <div class="abs thumb" role="img" aria-label="Green reinforcement grid close-up" style="left:424px;top:927px;background:#5e7a3c"></div>
  <div class="abs thumb" role="img" aria-label="Mesh with plants" style="left:504px;top:927px;background:#6b8f4a"></div>
  <div class="abs thumb" role="img" aria-label="Grid panels on a driveway" style="left:344px;top:989px;background:#7f8aa0"></div>
  <div class="abs thumb" role="img" aria-label="Planted grid section" style="left:424px;top:989px;background:#8f7a4a"></div>
  <div class="abs thumb" role="img" aria-label="Car parked on gravel driveway" style="left:504px;top:989px;background:#9a9a9a"></div>

  <div class="abs f-text" style="left:605px;top:922px;width:230px;line-height:19.5px">PONDERMESH ECO SOLUTIONS LTD<br>Brackenfold House, Kelmere Ind Est, Ashbridge, AB1 2CD</div>
  <div class="abs" style="left:605px;top:988px;font-size:15px;font-weight:600;line-height:19px"><div class="g">0100-555-0182</div><div class="o">0800-555-0145</div></div>

  <div class="abs social" aria-label="Social link 1" style="left:852px;background:#3b5998"></div>
  <div class="abs social" aria-label="Social link 2" style="left:900px;background:#1fb9e6"></div>
  <div class="abs social" aria-label="Social link 3" style="left:948px;background:#d23a2f"></div>

  <div class="abs card" style="left:851px">Paylo</div>
  <div class="abs card" style="left:901px">Mintcard</div>
  <div class="abs card" style="left:951px">Orbito</div>
  <div class="abs card" style="left:1001px">Tallypay</div>

  <div class="abs bottom"></div>
  <div class="abs bottom-left">© 2016 &nbsp;pondermesh eco solutions ltd</div>
  <div class="abs bottom-links"><span>Site Map</span><span>Email Terms of Service</span><span>Delivery and Returns</span></div>
</footer>

</body>
</html>
```